Business Card Design (NEW FILES)

ATTENTION: New vector files are available. Please update your design to reflect/use the new (better resolution) logo images.

Seeking a unique and professional business card design for a commercial drone photography/videography business. The layout should feature
the logo (attached) and include the following information:
Owen Tarrick
614-502-7738
www.skylarkreelworks.example
NRD Certified Remote Pilot

Owen Tarrick

```html
<!DOCTYPE html>
<html lang="en">
<head>
<meta charset="utf-8">
<title>Skylark Reelworks – Business Card</title>
<link rel="stylesheet" href="https://fonts.googleapis.com/css2?family=Poppins:wght@400;500;600&display=swap">
<style>
  :root {
    --bg: #4a5a8e;
    --navy: #1a1d4e;
    --orange: #ef8a3c;
    --white: #ffffff;
    --ink: #1f2250;
  }
  * { margin: 0; padding: 0; box-sizing: border-box; }
  html, body { width: 1200px; height: 876px; overflow: hidden; }
  body {
    background: var(--bg);
    font-family: "Poppins", sans-serif;
    position: relative;
  }
  .card {
    position: absolute;
    top: 288px;
    width: 525px;
    height: 300px;
    border-radius: 4px;
    overflow: hidden;
    box-shadow: 0 10px 24px rgba(10, 15, 45, 0.35);
  }
  .card--front { left: 50px; background: var(--white); }
  .card--back { left: 625px; background: var(--navy); }

  .contact-block { position: absolute; left: 38px; top: 30px; }
  .person-name {
    font-size: 21px; font-weight: 500; color: var(--ink);
    letter-spacing: 0.5px; text-transform: uppercase; line-height: 1.1;
  }
  .person-role { font-size: 11px; color: var(--orange); margin-bottom: 10px; }
  .contact-list { list-style: none; }
  .contact-list li {
    display: flex; align-items: center; gap: 7px;
    font-size: 12px; color: var(--ink); line-height: 1.7;
  }
  .contact-list svg { width: 10px; height: 10px; fill: var(--orange); flex: none; }

  .credential-band {
    position: absolute; left: 0; bottom: 28px;
    width: 236px; height: 68px;
    background: var(--navy);
    border-radius: 0 34px 34px 0;
    border-bottom: 3px solid var(--orange);
    padding: 14px 0 0 30px;
    color: var(--white); font-size: 12px; line-height: 1.55;
  }

  .brand {
    position: absolute; display: flex; align-items: center; gap: 10px;
    font-weight: 500; text-transform: uppercase; letter-spacing: 1px;
    white-space: nowrap;
  }
  .brand-dot { width: 13px; height: 13px; border-radius: 50%; background: var(--orange); flex: none; }
  .card--front .brand { right: 30px; top: 162px; font-size: 22px; color: var(--ink); }
  .card--back .brand { left: 50%; top: 50%; transform: translate(-50%, -50%); font-size: 26px; color: var(--white); }
</style>
</head>
<body>
  <section class="card card--front" aria-label="Business card front">
    <div class="contact-block">
      <h1 class="person-name">Owen Tarrick</h1>
      <p class="person-role">Owner</p>
      <ul class="contact-list">
        <li><svg viewBox="0 0 24 24"><path d="M6.6 10.8a15.1 15.1 0 0 0 6.6 6.6l2.2-2.2a1 1 0 0 1 1-.25 11.4 11.4 0 0 0 3.6.57 1 1 0 0 1 1 1V20a1 1 0 0 1-1 1A17 17 0 0 1 3 4a1 1 0 0 1 1-1h3.5a1 1 0 0 1 1 1c0 1.25.2 2.45.57 3.57a1 1 0 0 1-.25 1z"/></svg>614-502-7738</li>
        <li><svg viewBox="0 0 24 24"><path d="M2 5h20v14H2zM4 7v.5l8 5 8-5V7z"/></svg>ot@skylarkreelworks.example</li>
        <li><svg viewBox="0 0 24 24"><circle cx="12" cy="12" r="10"/></svg>www.skylarkreelworks.example</li>
      </ul>
    </div>
    <div class="credential-band">
      <p>NRD Certified Remote Pilot</p>
      <p>Fully Insured</p>
    </div>
    <div class="brand"><span class="brand-dot"></span>Skylark Reelworks</div>
  </section>

  <section class="card card--back" aria-label="Business card back">
    <div class="brand"><span class="brand-dot"></span>Skylark Reelworks</div>
  </section>
</body>
</html>
```